Online business manager needs a website

I need a website designed and then coded. I am an online business manager serving a number of different industries providing administrative support to existing small businesses and helping solo practitioners get their new business up and running.

I didn't have a logo formally designed but have been using the attached avatar and wouldn't mind something that incorporated that.

The business doesn't have an official name, so I've just been using my name Lena Morvath, Online Business Manager or Lena Morvath, OBM. I've attached two documents that I have made previously for an example of content.

I would prefer the final site be in Wordpress.

Requirements
Must have
• A way to contact me, testimonials, list of services

```html
<!DOCTYPE html>
<html lang="en">
<head>
<meta charset="UTF-8">
<title>Lena Morvath – Online Business Manager</title>
<link href="https://fonts.googleapis.com/css2?family=Roboto+Condensed:wght@300;400;700&family=Poppins:wght@400;500;600;700&display=swap" rel="stylesheet">
<style>
:root{
  --purple:#4a1a88;
  --purple-deep:#2b0b55;
  --purple-bright:#5b22a8;
  --lavender:#c3ccff;
  --mint:#eef9f8;
  --field:#dff4f0;
  --ink:#1d1d1d;
  --muted:#444;
  --dark:#0d0d0f;
  --white:#ffffff;
}
*{box-sizing:border-box;margin:0;padding:0}
html,body{width:1200px;height:5164px;overflow:hidden}
body{font-family:"Poppins",sans-serif;color:var(--ink);background:var(--mint)}
.page{position:relative;width:1200px;height:5164px;overflow:hidden}
.abs{position:absolute}
.heading{font-family:"Roboto Condensed",sans-serif;font-weight:400;font-size:44px;letter-spacing:.5px;text-transform:uppercase}
.btn{position:absolute;display:flex;align-items:center;justify-content:center;border-radius:22px;font-size:12px;font-weight:500}
.btn-purple{background:var(--purple);color:var(--white)}
.btn-mint{background:var(--field);color:var(--purple-deep)}
.photo{position:absolute}
.hex{clip-path:polygon(50% 0,100% 25%,100% 75%,50% 100%,0 75%,0 25%)}

/* hero */
.hero{position:absolute;left:0;top:0;width:1200px;height:620px;background:linear-gradient(135deg,#2a0a52 0%,#3d1672 55%,#4a1c86 100%)}
.brand{position:absolute;display:flex;align-items:center;gap:10px;color:var(--white)}
.brand-dot{width:44px;height:44px;border:2px solid var(--white);border-radius:50%}
.brand-name{font-family:"Roboto Condensed",sans-serif;font-size:36px;line-height:1;text-transform:uppercase}
.brand-sub{font-size:12px;margin-top:3px}
.hero-title{position:absolute;left:140px;top:152px;font-family:"Roboto Condensed",sans-serif;font-weight:700;font-size:72px;line-height:78px;color:var(--white);text-transform:uppercase;letter-spacing:-.5px}
.hero-title span{color:var(--lavender)}
.hero-sub{position:absolute;left:140px;top:320px;font-family:"Roboto Condensed",sans-serif;font-size:24px;line-height:30px;color:var(--white);text-transform:uppercase}

/* services */
.service{position:absolute;width:216px;height:156px;background:var(--white);box-shadow:0 2px 10px rgba(0,0,0,.08);display:flex;flex-direction:column;align-items:center;justify-content:center;gap:14px;font-size:14px;font-weight:500}
.service svg{width:52px;height:52px;stroke:var(--purple);fill:none;stroke-width:2}

/* about */
.about-text{position:absolute;left:594px;top:1350px;width:466px;color:#ddd;font-size:12.5px;line-height:21px}
.about-text p{margin-bottom:14px}
.about-text .strong{color:var(--white);font-weight:500;font-size:13px}
.contact-chip{position:absolute;display:flex;align-items:center;gap:10px;color:#eee;font-size:12px;line-height:17px}
.chip-icon{width:38px;height:38px;border-radius:50%;background:var(--white);display:flex;align-items:center;justify-content:center}
.chip-icon svg{width:18px;height:18px;fill:var(--purple)}

/* hex cards */
.hex-card{position:absolute;width:262px;height:302px;display:flex;flex-direction:column;align-items:center;justify-content:center;gap:14px;font-size:20px;font-weight:500;text-align:center;line-height:26px}
.hex-card svg{width:90px;height:90px;fill:none;stroke-width:3}
.hex-light{background:var(--white);color:var(--ink)}
.hex-light svg{stroke:var(--purple)}
.hex-dark{background:var(--purple);color:var(--white)}
.hex-dark svg{stroke:var(--white)}

/* rates */
.rate{position:absolute;top:3235px;width:216px;height:214px;background:var(--white);box-shadow:0 2px 10px rgba(0,0,0,.08);text-align:center;padding-top:24px}
.rate-price{font-size:30px;font-weight:700;color:var(--purple)}
.rate-unit{font-size:13px;margin-top:2px}
.rate-desc{font-size:14px;font-weight:500;line-height:21px;margin-top:24px;padding:0 18px}
.rate-resp{font-size:12px;margin-top:14px}

/* testimonial */
.quote-card{position:absolute;left:282px;top:3808px;width:636px;height:238px;background:var(--white);text-align:center;font-size:12.5px;line-height:22px;padding:44px 30px 0}

/* form */
.field{position:absolute;background:var(--field);font-size:11px;color:#333;padding:12px 20px}

/* footer */
.foot-item{position:absolute;top:5024px;display:flex;align-items:center;gap:12px;color:var(--white);font-size:12px;line-height:18px}
.foot-icon{width:38px;height:38px;border-radius:50%;background:var(--white);display:flex;align-items:center;justify-content:center}
.foot-icon svg{width:18px;height:18px;fill:var(--purple)}
</style>
</head>
<body>
<div class="page">

  <!-- HERO -->
  <section class="hero"></section>
  <div class="photo" role="img" aria-label="Portrait of Lena Morvath smiling in a yellow top" style="left:640px;top:92px;width:470px;height:510px;border-radius:235px 235px 0 0;background:radial-gradient(circle at 50% 38%,#d9a574 0%,#c58a55 30%,#e1b33a 65%,#3a1670 100%)"></div>
  <svg class="abs" style="left:0;top:500px" width="1200" height="120" viewBox="0 0 1200 120">
    <polygon points="0,10 1200,105 1200,120 0,120" fill="var(--mint)"/>
    <polygon points="0,10 1200,105 1200,110 0,42" fill="var(--purple-bright)"/>
  </svg>
  <div class="brand" style="left:140px;top:28px">
    <div class="brand-dot"></div>
    <div><div class="brand-name">Lena Morvath</div><div class="brand-sub">Online Business Manager</div></div>
  </div>
  <div class="btn btn-mint" style="left:930px;top:16px;width:128px;height:40px">Contact Me</div>
  <h1 class="hero-title">Online <span>Business</span><br>Manager</h1>
  <p class="hero-sub">Serving a number of different industries<br>providing administrative support.</p>
  <div class="btn btn-mint" style="left:140px;top:410px;width:128px;height:42px">Contact Me</div>

  <!-- WHAT I DO BEST -->
  <h2 class="heading abs" style="left:0;width:1200px;top:668px;text-align:center">What I Do Best</h2>
  <div class="service" style="left:140px;top:746px"><svg viewBox="0 0 52 52"><rect x="8" y="8" width="36" height="28" rx="2"/><path d="M14 44h24M26 36v8M16 18h20M16 26h12"/></svg>Content Repurposing</div>
  <div class="service" style="left:374px;top:748px"><svg viewBox="0 0 52 52"><path d="M8 44h36M12 44V32M20 44V26M28 44V30M36 44V20M10 26l10-8 8 6 14-12"/></svg>Financial Analytics</div>
  <div class="service" style="left:608px;top:748px"><svg viewBox="0 0 52 52"><rect x="10" y="6" width="32" height="24" rx="2"/><path d="M16 14h20M16 20h14M8 46c0-8 6-12 18-12s18 4 18 12"/></svg>Data Entry</div>
  <div class="service" style="left:842px;top:748px"><svg viewBox="0 0 52 52"><circle cx="10" cy="12" r="4"/><circle cx="42" cy="12" r="4"/><circle cx="26" cy="8" r="4"/><path d="M14 12h8M30 12h8M26 12v18M18 44l8-14 8 14z"/></svg>Graphic Creations</div>
  <div class="service" style="left:258px;top:914px"><svg viewBox="0 0 52 52"><circle cx="26" cy="26" r="18"/><rect x="16" y="19" width="20" height="14"/><path d="M16 19l10 8 10-8"/></svg>Email Management</div>
  <div class="service" style="left:492px;top:914px"><svg viewBox="0 0 52 52"><circle cx="22" cy="30" r="10"/><circle cx="22" cy="30" r="4"/><circle cx="36" cy="14" r="7"/><path d="M22 16v4M22 40v4M8 30h4M32 30h4"/></svg>Project Management</div>
  <div class="service" style="left:726px;top:914px"><svg viewBox="0 0 52 52"><rect x="12" y="6" width="28" height="40" rx="2"/><path d="M18 14h16M18 22h16M18 30h10M18 38h6"/></svg>Bookkeeping</div>
  <div class="btn btn-purple" style="left:536px;top:1105px;width:128px;height:42px">Contact Me</div>

  <!-- ABOUT -->
  <svg class="abs" style="left:0;top:1190px" width="1200" height="770" viewBox="0 0 1200 770">
    <polygon points="0,108 1200,0 1200,648 0,760" fill="#121214"/>
    <polygon points="0,108 1200,0 1200,160 0,300" fill="#1c1c20"/>
    <polygon points="0,720 1200,640 1200,660 0,770" fill="var(--purple)"/>
  </svg>
  <div class="photo hex" role="img" aria-label="Close-up portrait of Lena Morvath in glasses among pink flowers" style="left:140px;top:1355px;width:406px;height:406px;background:radial-gradient(circle at 50% 48%,#d9b69a 0%,#c99474 32%,#b0407a 62%,#5a2a3a 100%)"></div>
  <h2 class="heading abs" style="left:594px;top:1346px;color:var(--white)">About Me</h2>
  <div class="about-text" style="top:1412px">
    <p>I am focused on the live event and entertainment industry. Helping artists and owners to better manage their career and business by strategically reviewing systems, recommending operational efficiencies, &amp; managing inboxes</p>
    <p>Helping businesses achieve their goals is my passion, and I'm thrilled that with my assistance you will have more time for your own passion project. I thrive while working independently, which means you can be confident when leaving tasks for me.</p>
    <p>The type of work that lights me up is anything involving organization and/or spreadsheets. You need data analyzed that includes multiple nested if formulas?</p>
    <p class="strong">You Have An Overwhelming Amount of Email To Sort Through And Appointments To Book? I'm Your Gal!</p>
  </div>
  <div class="contact-chip" style="left:590px;top:1754px">
    <div class="chip-icon"><svg viewBox="0 0 24 24"><path d="M3 6h18v12H3z M3 6l9 7 9-7" fill="none" stroke="var(--purple)" stroke-width="2"/></svg></div>
    <div>E-mail<br>lena.morvath@mailbox.net</div>
  </div>
  <div class="contact-chip" style="left:834px;top:1754px">
    <div class="chip-icon"><svg viewBox="0 0 24 24"><path d="M6.6 10.8a15 15 0 0 0 6.6 6.6l2.2-2.2c.3-.3.7-.4 1-.2 1.1.4 2.3.6 3.6.6.6 0 1 .4 1 1V20c0 .6-.4 1-1 1A17 17 0 0 1 3 4c0-.6.4-1 1-1h3.5c.6 0 1 .4 1 1 0 1.3.2 2.5.6 3.6.1.3 0 .7-.2 1z"/></svg></div>
    <div>Phone<br>555 014 2286</div>
  </div>

  <!-- EDUCATION / SKILLS / ACCREDITATION -->
  <div class="hex-card hex hex-light" style="left:150px;top:2003px"><svg viewBox="0 0 90 90"><path d="M8 32l37-16 37 16-37 16z M24 40v20c6 6 36 6 42 0V40 M82 32v22"/></svg>MY<br>EDUCATION</div>
  <div class="hex-card hex hex-dark" style="left:472px;top:2003px"><svg viewBox="0 0 90 90"><rect x="8" y="8" width="28" height="16" rx="3"/><rect x="50" y="8" width="32" height="20" rx="2"/><path d="M56 24V18M64 24V14M72 24V16"/><circle cx="36" cy="54" r="16"/><circle cx="36" cy="54" r="6"/><circle cx="64" cy="62" r="10"/></svg>MY<br>SKILLS</div>
  <div class="hex-card hex hex-light" style="left:794px;top:2003px"><svg viewBox="0 0 90 90"><rect x="12" y="8" width="66" height="52"/><path d="M22 20h46M22 30h46"/><circle cx="45" cy="58" r="12"/><path d="M38 68l-4 16 11-6 11 6-4-16"/></svg>MY<br>ACCREDITATION</div>
  <div btn class="btn btn-purple" style="left:536px;top:2340px;width:128px;height:42px">Contact Me</div>

  <!-- MY WORK -->
  <svg class="abs" style="left:0;top:2468px" width="1200" height="640" viewBox="0 0 1200 640">
    <rect x="0" y="0" width="1200" height="560" fill="#111113"/>
    <polygon points="0,530 1200,560 1200,640 0,560" fill="var(--purple)"/>
    <polygon points="0,560 1200,640 1200,640 0,640" fill="var(--mint)"/>
  </svg>
  <h2 class="heading abs" style="left:0;width:1200px;top:2548px;text-align:center;color:var(--white)">My Work</h2>
  <div class="photo" role="img" aria-label="Portfolio slide: simple ways to look great on video calls" style="left:206px;top:2650px;width:160px;height:276px;background:linear-gradient(180deg,#ff8a3c 0%,#ff8a3c 62%,#b9a89a 100%)"></div>
  <div class="photo" role="img" aria-label="Portfolio slide: podcast promo graphic for owning your business workflows and automations" style="left:364px;top:2632px;width:472px;height:308px;background:linear-gradient(135deg,#fdf2e8 0%,#f7e2d2 100%)"></div>
  <div class="photo" role="img" aria-label="Portfolio slide: playful dog photo with quote text" style="left:836px;top:2650px;width:158px;height:276px;background:linear-gradient(135deg,#e9ddc0 0%,#bfa880 50%,#6e8a4c 100%)"></div>
  <svg class="abs" style="left:123px;top:2768px" width="42" height="42" viewBox="0 0 42 42"><circle cx="21" cy="21" r="19" fill="none" stroke="#fff" stroke-width="2"/><path d="M28 21H14M19 15l-6 6 6 6" fill="none" stroke="#fff" stroke-width="2.5"/></svg>
  <svg class="abs" style="left:1037px;top:2768px" width="42" height="42" viewBox="0 0 42 42"><circle cx="21" cy="21" r="20" fill="#fff"/><path d="M14 21h14M23 15l6 6-6 6" fill="none" stroke="var(--purple)" stroke-width="2.5"/></svg>

  <!-- RATES -->
  <h2 class="heading abs" style="left:0;width:1200px;top:3158px;text-align:center">Rates and Packages</h2>
  <div class="rate" style="left:140px"><div class="rate-price">$40</div><div class="rate-unit">Hourly Rate</div><div class="rate-desc">For Clients Needing Only Occasional Help</div></div>
  <div class="rate" style="left:374px"><div class="rate-price">$700</div><div class="rate-unit">20 hours/month</div><div class="rate-desc">Includes One 15 Minute Meeting Per Week</div><div class="rate-resp">Responses Within 72 Hours</div></div>
  <div class="rate" style="left:608px"><div class="rate-price">$1,300</div><div class="rate-unit">40 hours/month</div><div class="rate-desc">Includes One 30 Minute Meeting Per Week</div><div class="rate-resp">Responses Within 48 Hours</div></div>
  <div class="rate" style="left:842px"><div class="rate-price">$2,400</div><div class="rate-unit">80 hours/month</div><div class="rate-desc">Includes One 60 Minute Meeting Per Week</div><div class="rate-resp">Responses Within 24 Hours</div></div>
  <div class="btn btn-purple" style="left:534px;top:3490px;width:128px;height:42px">Get Started</div>

  <!-- CLIENTS LOVE -->
  <svg class="abs" style="left:0;top:3560px" width="1200" height="700" viewBox="0 0 1200 700">
    <polygon points="0,120 1200,0 1200,570 0,690" fill="#111113"/>
    <polygon points="0,120 1200,0 1200,240 0,330" fill="#232327"/>
    <polygon points="0,690 1200,570 1200,590 0,700" fill="var(--purple-bright)"/>
    <polygon points="0,650 1200,555 1200,575 0,690" fill="var(--purple-deep)"/>
  </svg>
  <h2 class="heading abs" style="left:0;width:1200px;top:3714px;text-align:center;color:var(--white)">Clients Love</h2>
  <div class="abs" style="left:318px;top:4040px;width:564px;height:20px;background:#bdbdbd"></div>
  <div class="quote-card">
    <p>When it became apparent that a project would take more time than I had, Lena stepped up to take on the required research.</p>
    <p style="margin-top:8px">She was thorough and timely; able to meet a last-minute 12-hour deadline. I would highly recommend Lena to assist with your next project.</p>
    <p style="font-size:14px;font-weight:500;margin-top:6px">Dana R.</p>
    <p style="font-size:10px;line-height:16px">Owner, Northgate Roofing</p>
    <svg style="margin-top:6px" width="46" height="14" viewBox="0 0 46 14"><path d="M20 7H4M9 2L4 7l5 5" fill="none" stroke="#555" stroke-width="1.5"/><path d="M26 7h16M37 2l5 5-5 5" fill="none" stroke="var(--purple)" stroke-width="1.5"/></svg>
  </div>
  <svg class="abs" style="left:573px;top:3782px" width="54" height="54" viewBox="0 0 54 54"><circle cx="27" cy="27" r="26" fill="var(--mint)"/><path d="M16 32c0-6 3-10 8-12v4c-2 1-3 3-3 5h3v7h-8zM29 32c0-6 3-10 8-12v4c-2 1-3 3-3 5h3v7h-8z" fill="var(--purple)"/></svg>

  <!-- QUICK ME -->
  <div class="abs" style="left:0;top:4250px;width:1200px;height:520px;background:var(--mint)"></div>
  <div class="photo hex" role="img" aria-label="Portrait of Lena Morvath with long hair outdoors in the city" style="left:650px;top:4272px;width:436px;height:440px;background:radial-gradient(circle at 50% 45%,#e3b896 0%,#d1a06a 30%,#8a6a4a 60%,#3c3b40 100%)"></div>
  <h2 class="heading abs" style="left:140px;top:4318px">Quick Me</h2>
  <div class="field" style="left:140px;top:4390px;width:230px;height:42px">First Name*</div>
  <div class="field" style="left:382px;top:4390px;width:226px;height:42px">Latest Name*</div>
  <div class="field" style="left:140px;top:4450px;width:230px;height:42px">Email*</div>
  <div class="field" style="left:382px;top:4450px;width:226px;height:42px">Phone*</div>
  <div class="field" style="left:140px;top:4510px;width:468px;height:90px">Message</div>
  <div class="btn btn-purple" style="left:140px;top:4640px;width:128px;height:42px">Submit Now</div>

  <!-- FOOTER -->
  <svg class="abs" style="left:0;top:4760px" width="1200" height="404" viewBox="0 0 1200 404">
    <rect x="0" y="0" width="1200" height="404" fill="#0e0e10"/>
    <polygon points="0,0 1200,0 1200,96 0,20" fill="var(--mint)"/>
    <polygon points="0,20 1200,96 1200,110 0,42" fill="var(--purple)"/>
  </svg>
  <div class="brand" style="left:456px;top:4896px">
    <div class="brand-dot" style="width:64px;height:64px"></div>
    <div><div class="brand-name" style="font-size:46px">Lena Morvath</div><div class="brand-sub" style="font-size:15px">Online Business Manager</div></div>
  </div>
  <div class="foot-item" style="left:140px"><div class="foot-icon"><svg viewBox="0 0 24 24"><path d="M3 6h18v12H3z M3 6l9 7 9-7" fill="none" stroke="var(--purple)" stroke-width="2"/></svg></div><div>E-mail<br>lena.morvath@mailbox.net</div></div>
  <div class="foot-item" style="left:455px"><div class="foot-icon"><svg viewBox="0 0 24 24"><path d="M6.6 10.8a15 15 0 0 0 6.6 6.6l2.2-2.2c.3-.3.7-.4 1-.2 1.1.4 2.3.6 3.6.6.6 0 1 .4 1 1V20c0 .6-.4 1-1 1A17 17 0 0 1 3 4c0-.6.4-1 1-1h3.5c.6 0 1 .4 1 1 0 1.3.2 2.5.6 3.6.1.3 0 .7-.2 1z"/></svg></div><div>Phone No<br>555 014 2286</div></div>
  <div class="foot-item" style="left:692px"><div class="foot-icon"></div><div>LinkedIn<br>Lena Morvath</div></div>
  <div class="foot-item" style="left:934px"><div class="foot-icon"></div><div>Facebook<br>/LenaMorvath</div></div>
  <div class="abs" style="left:140px;top:5112px;width:920px;height:1px;background:#444"></div>
  <p class="abs" style="left:0;width:1200px;top:5128px;text-align:center;color:#ddd;font-size:12px">© 2023 Lena Morvath. All Rights Reserved.</p>

</div>
</body>
</html>
```